Business cards - BRENT Roofing & Siding

We need simple business cards made up for our Roofing & Siding business based in Calgary Alberta.
The logo on one side of the card and potentially our slogan "Built with trust, verified by time".
The other side could have:
-A small logo
-Rep name:
-Rep cell phone:
-Rep email:
-Office phone: 403-684-2093
-Website: PrairieShingleWorks.com

We would like to incorporate the colours from our logo, especially the lite blue on the jpeg file. I have attached the ai file and jpeg file. We like the colours better on the jpeg file.

I do not require a money back guarantee

```html
<!DOCTYPE html>
<html lang="en">
<head>
<meta charset="UTF-8">
<title>BRENT Roofing &amp; Siding – Business Card</title>
<link href="https://fonts.googleapis.com/css2?family=Oswald:wght@500&family=Montserrat:wght@400;500&display=swap" rel="stylesheet">
<style>
  :root {
    --stage: #2b2725;
    --card: #1d1e20;
    --card-light: #2a2b2e;
    --edge-red: #c4161c;
    --brand-blue: #1b8fe6;
    --text-white: #f2f2f2;
  }
  * { box-sizing: border-box; margin: 0; padding: 0; }
  html, body {
    width: 1200px;
    height: 716px;
    overflow: hidden;
    background: var(--stage);
  }
  .stage {
    position: relative;
    width: 1200px;
    height: 716px;
    display: flex;
    align-items: center;
    justify-content: center;
    gap: 48px;
  }
  .card {
    position: relative;
    width: 530px;
    height: 303px;
    background: linear-gradient(135deg, var(--card-light) 0%, var(--card) 55%);
    border: 3px solid var(--edge-red);
    border-radius: 4px;
    box-shadow: 0 14px 30px rgba(0,0,0,0.45);
  }
  /* Front */
  .card-front {
    display: flex;
    align-items: center;
    justify-content: center;
  }
  .brand-lockup {
    display: flex;
    align-items: center;
    gap: 14px;
  }
  .brand-square {
    width: 22px;
    height: 22px;
    background: var(--brand-blue);
  }
  .brand-name {
    font-family: "Montserrat", sans-serif;
    font-weight: 500;
    font-size: 30px;
    letter-spacing: 1px;
    color: var(--text-white);
  }
  /* Back */
  .card-back {
    display: flex;
    align-items: center;
    padding-left: 40px;
  }
  .rep {
    text-align: right;
    width: 190px;
  }
  .rep-name {
    font-family: "Oswald", sans-serif;
    font-weight: 500;
    font-size: 34px;
    line-height: 1;
    color: var(--brand-blue);
    text-transform: uppercase;
    letter-spacing: 0.5px;
  }
  .rep-title {
    font-family: "Montserrat", sans-serif;
    font-size: 15px;
    color: var(--text-white);
    margin-top: 6px;
    letter-spacing: 0.5px;
  }
  .divider {
    width: 2px;
    height: 90px;
    background: var(--brand-blue);
    margin: 0 18px;
  }
  .contact-list {
    list-style: none;
    font-family: "Montserrat", sans-serif;
    font-size: 15px;
    color: var(--text-white);
  }
  .contact-list li {
    display: flex;
    align-items: center;
    gap: 8px;
    line-height: 24px;
  }
  .contact-icon {
    width: 12px;
    height: 12px;
    flex: none;
  }
</style>
</head>
<body>
<main class="stage">
  <section class="card card-front" aria-label="Card front">
    <div class="brand-lockup">
      <span class="brand-square"></span>
      <span class="brand-name">BRENT Roofing &amp; Siding</span>
    </div>
  </section>

  <section class="card card-back" aria-label="Card back">
    <div class="rep">
      <p class="rep-name">Daniel Harper</p>
      <p class="rep-title">DIRECTOR</p>
    </div>
    <span class="divider"></span>
    <ul class="contact-list">
      <li>
        <svg class="contact-icon" viewBox="0 0 12 12" aria-hidden="true"><path d="M2.5 1l2 2.4-1.2 1.3a7 7 0 0 0 4 4l1.3-1.2L11 9.5 9.6 11C5 10.6 1.4 7 1 2.4z" fill="#1b8fe6"/></svg>
        403-684-2093
      </li>
      <li>
        <svg class="contact-icon" viewBox="0 0 12 12" aria-hidden="true"><rect x="3" y="0.8" width="6" height="10.4" rx="1" fill="none" stroke="#1b8fe6" stroke-width="1.2"/><circle cx="6" cy="9.4" r="0.6" fill="#1b8fe6"/></svg>
        905-312-4478
      </li>
      <li>
        <svg class="contact-icon" viewBox="0 0 12 12" aria-hidden="true"><rect x="0.8" y="2.5" width="10.4" height="7" fill="none" stroke="#1b8fe6" stroke-width="1.2"/><path d="M1 3l5 3.6L11 3" fill="none" stroke="#1b8fe6" stroke-width="1.2"/></svg>
        brentroof@prairiemail.net
      </li>
      <li>
        <svg class="contact-icon" viewBox="0 0 12 12" aria-hidden="true"><circle cx="6" cy="6" r="5" fill="none" stroke="#1b8fe6" stroke-width="1.1"/><ellipse cx="6" cy="6" rx="2.2" ry="5" fill="none" stroke="#1b8fe6" stroke-width="1"/><path d="M1 6h10" stroke="#1b8fe6" stroke-width="1"/></svg>
        PrairieShingleWorks.com
      </li>
    </ul>
  </section>
</main>
</body>
</html>
```